Website for Vornelix Capital, my new firm that raises money from investors to buy, build, own an...

Vornelix Capital needs a website! We are a new company with very experienced people, who invest in, own and build hotel properties, as well as apartments and other commercial real estate. We seek investors for our projects, and we provide safe, secure returns on their investment in our projects. Our new logo is designed to exhibit strength, class and security, and would like our website to continue on this theme. Our name, Vornelix, is a word-play on a Greek word “aristeia”, which means “excellence” and “a warriors finest moment of glory in war”. If you are in business, you realize that much of it is like war, with strategy and moves and opponents and competitors, and ever-changing economic conditions and threats that make business very much like war. We like to think that we are good at business (war), and so have named our company “Vornelix”, using the founders last name and the word “aristeia” combined. Another definition of "aristeia" is "performing at the peak of one's potential after a long struggle"...again, much like business in real life! The website design should exhibit financial security, smart moves, and positive growth towards a bright future.

Target Market(s)

The target market is smart and wealthy investors, with others such as brokers, cities and government agencies, lenders, sellers, partners, etc also looking at it.

Industry/Entity Type

Investment

Number of Pages Required

5+ page

Font styles to use
Sans Serif

Colors
fec214

Requirements
Must have
• Our website should have a landing page, a "about" or bio page, a projects page and a contact us page. Our new logo uses the colors black and gold, so this should be factored in to our site. The site should be simple, yet impactful and impressive. I have actually two logos, which can be mixed and interchanged in a complimentary way, each with their own unique look.
Nice to have
• I have uploaded a couple screenshots of a website i like, and the simplicity I mention.
Should not have
• The site should not be flashy or complicated or complex or "busy"

```html
<!DOCTYPE html>
<html lang="en">
<head>
<meta charset="utf-8">
<title>Vornelix Capital</title>
<link href="https://fonts.googleapis.com/css2?family=Lato:wght@400;700;900&family=Montserrat:wght@400;500;600&family=Open+Sans:wght@400;600&display=swap" rel="stylesheet">
<style>
:root{
  --gold:#c0932c;
  --gold-dark:#a97f22;
  --ink:#111;
  --navy:#0d1526;
  --grey-bg:#f7f7f7;
  --text-grey:#8a8a8a;
  --white:#fff;
  --footer:#050505;
}
*{margin:0;padding:0;box-sizing:border-box}
html,body{width:1200px;height:2647px;overflow:hidden}
body{position:relative;background:var(--white);font-family:'Open Sans',sans-serif;color:var(--ink)}
.abs{position:absolute}

/* top bar */
.topbar{left:0;top:0;width:1200px;height:51px;background:var(--gold);color:var(--white)}
.topbar .phone{left:732px;top:12px;font:700 21px 'Lato',sans-serif;display:flex;align-items:center;gap:8px}
.topbar .mail{left:944px;top:15px;font:400 16px 'Open Sans',sans-serif;display:flex;align-items:center;gap:8px}

/* nav */
.nav{left:0;top:51px;width:1200px;height:117px;background:var(--white)}
.brand{left:78px;top:42px;font:700 30px 'Montserrat',sans-serif;letter-spacing:1px;color:var(--ink);display:flex;align-items:center;gap:10px}
.brand .dot{width:14px;height:14px;background:var(--gold)}
.nav-item{top:24px;width:140px;margin-left:-70px;text-align:center;font:400 14px 'Montserrat',sans-serif;color:#b5b5b5}
.nav-item .mark{display:block;width:46px;height:46px;margin:0 auto 4px;border:2px solid #e2e2e2;border-radius:50%}
.nav-item.active{color:#2e5dbf}
.nav-item.active .mark{border-color:var(--gold)}

/* hero */
.hero{left:0;top:168px;width:1200px;height:570px;background:linear-gradient(180deg,#0a0f1d 0%,#142238 55%,#2a3347 100%)}
.hero-title{left:0;top:300px;width:1200px;text-align:center;font:700 72px 'Lato',sans-serif;color:var(--white);letter-spacing:1px}
.hero-sub{left:280px;top:394px;width:640px;text-align:center;font:400 15.5px/1.35 'Open Sans',sans-serif;color:#d8dbe2}
.btn-light{background:var(--white);color:var(--ink);font:500 16px 'Montserrat',sans-serif;display:flex;align-items:center;justify-content:center}
.hero-btn{left:485px;top:455px;width:230px;height:50px}
.gold-line{left:0;top:734px;width:1200px;height:6px;background:var(--gold)}

/* features */
.feature{top:640px;width:300px;margin-left:-150px;text-align:center}
.feature .badge{width:150px;height:150px;border-radius:50%;background:var(--gold);border:5px solid #8f6c1d;margin:0 auto;display:flex;align-items:center;justify-content:center}
.feature h3{margin-top:56px;font:600 19px 'Montserrat',sans-serif;color:var(--ink)}

/* about */
.about{left:0;top:953px;width:1200px;height:521px;background:var(--grey-bg)}
.eyebrow{font:400 15px 'Montserrat',sans-serif;color:var(--text-grey)}
.about .eyebrow{left:79px;top:87px}
.about-title{left:79px;top:110px;font:400 38px 'Montserrat',sans-serif;color:var(--ink)}
.about-title span{color:var(--gold);font-weight:500}
.about-text{left:79px;top:177px;width:610px;font:400 16px/23px 'Open Sans',sans-serif;color:var(--text-grey)}
.about-text p+p{margin-top:23px}
.btn-gold{left:76px;top:383px;width:175px;height:51px;background:var(--gold);color:var(--white);font:400 19px 'Montserrat',sans-serif;display:flex;align-items:center;justify-content:center}

.quote{left:766px;top:60px;width:357px;height:399px;background:linear-gradient(160deg,#1b2840 0%,#0e1626 60%,#1d2a3c 100%)}
.quote h2{position:absolute;left:34px;top:42px;font:400 23px 'Montserrat',sans-serif;color:var(--white)}
.field{position:absolute;left:34px;width:291px;height:36px;background:linear-gradient(180deg,#fff 0%,#f7f2e4 100%);border-radius:3px;display:flex;align-items:center;gap:10px;padding-left:12px;font:400 13px 'Open Sans',sans-serif;color:var(--gold)}
.field.msg{height:67px;align-items:flex-start;padding-top:10px}
.quote .btn-light{position:absolute;left:64px;top:295px;width:227px;height:35px;font-size:15px}

/* projects */
.projects .eyebrow{left:0;top:1548px;width:1200px;text-align:center;font-size:14px}
.projects-title{left:0;top:1570px;width:1200px;text-align:center;font:400 34px 'Montserrat',sans-serif}
.projects-title span{color:var(--gold);font-weight:500;font-size:38px}
.photo{position:absolute}
.feature-card{left:434px;top:1973px;width:689px;height:313px;background:linear-gradient(180deg,#3a2a22 0%,#2a2220 60%,#4a3426 100%);border:8px solid #8fb4dd}
.feature-card .overlay{position:absolute;inset:0;background:rgba(25,25,30,.55);text-align:center;color:var(--white)}
.overlay .label{margin-top:92px;font:400 22px 'Montserrat',sans-serif;color:#d9d9d9}
.overlay h3{margin-top:4px;font:500 40px 'Montserrat',sans-serif}
.overlay p{width:560px;margin:14px auto 0;font:400 14px/22px 'Open Sans',sans-serif;color:#cfcfcf}

/* footer */
.footer{left:0;top:2360px;width:1200px;height:235px;background:linear-gradient(180deg,#0b0b0b 0%,#111 100%)}
.footer-brand{left:78px;top:100px;font:700 26px 'Montserrat',sans-serif;color:var(--white);letter-spacing:1px;display:flex;align-items:center;gap:8px}
.footer-brand .dot{width:12px;height:12px;background:var(--white)}
.footer-about{left:270px;top:70px;width:112px;font:400 14px/19px 'Open Sans',sans-serif;color:#7c7c7c}
.divider{top:68px;width:2px;height:130px;background:#cfcfcf}
.contact-row{left:455px;display:flex;gap:16px;font:400 14px/19px 'Open Sans',sans-serif;color:#8a8a8a}
.contact-row svg{flex:none;margin-top:2px}
.links-title{left:822px;top:70px;font:400 17px 'Montserrat',sans-serif;color:var(--white)}
.links{top:108px;list-style:none;font:400 14px/20px 'Open Sans',sans-serif;color:#8a8a8a}
.links li::before{content:"• ";color:#8a8a8a}
.copyright{left:0;top:2595px;width:1200px;height:52px;background:var(--gold);display:flex;align-items:center;justify-content:center;font:400 15px 'Open Sans',sans-serif;color:#6a4f12}
.copyright strong{font:600 18px 'Montserrat',sans-serif;color:var(--ink);margin:0 6px}
</style>
</head>
<body>

<header>
  <div class="abs topbar">
    <div class="abs phone">
      <svg width="20" height="20" viewBox="0 0 24 24"><path fill="#fff" d="M6.6 10.8a15.1 15.1 0 0 0 6.6 6.6l2.2-2.2c.3-.3.7-.4 1-.2 1.1.4 2.3.6 3.6.6.6 0 1 .4 1 1V20c0 .6-.4 1-1 1C10.6 21 3 13.4 3 4c0-.6.4-1 1-1h3.5c.6 0 1 .4 1 1 0 1.3.2 2.5.6 3.6.1.3 0 .7-.2 1z"/></svg>
      (555) 014 2290
    </div>
    <div class="abs mail">
      <svg width="20" height="14" viewBox="0 0 20 14"><rect x="1" y="1" width="18" height="12" fill="none" stroke="#fff" stroke-width="1.5"/><path d="M1 1l9 7 9-7" fill="none" stroke="#fff" stroke-width="1.5"/></svg>
      info@vornelix.com
    </div>
  </div>

  <nav class="abs nav">
    <div class="abs brand"><span class="dot"></span>VORNELIX</div>
    <div class="abs nav-item active" style="left:630px"><span class="mark"></span>HOME</div>
    <div class="abs nav-item" style="left:768px"><span class="mark"></span>ABOUT US</div>
    <div class="abs nav-item" style="left:914px"><span class="mark"></span>PROJECT</div>
    <div class="abs nav-item" style="left:1073px"><span class="mark"></span>CONTACT US</div>
  </nav>
</header>

<section>
  <div class="abs hero" role="img" aria-label="Night city skyline with a rising stock chart line overlay"></div>
  <h1 class="abs hero-title">VORNELIX CAPITAL</h1>
  <p class="abs hero-sub">Vornelix Capital are a new company with very experienced people, who invest in, own and build hotel properties, as well as apartments and other commercial real estate.</p>
  <div class="abs btn-light hero-btn">GET STARTED NOW</div>
  <div class="abs gold-line"></div>

  <div class="abs feature" style="left:243px">
    <div class="badge">
      <svg width="64" height="64" viewBox="0 0 64 64"><path d="M20 28v-8a12 12 0 0 1 24 0v8" fill="none" stroke="#111" stroke-width="5"/><rect x="10" y="28" width="44" height="30" rx="3" fill="#111"/><text x="26" y="52" font-family="Lato,sans-serif" font-weight="900" font-size="22" fill="#c0932c">$</text><rect x="44" y="36" width="12" height="14" fill="#c0932c" stroke="#111" stroke-width="3"/></svg>
    </div>
    <h3>Financial Security</h3>
  </div>
  <div class="abs feature" style="left:600px">
    <div class="badge">
      <svg width="72" height="56" viewBox="0 0 72 56"><path d="M6 18h30M26 8l10 10-10 10" fill="none" stroke="#111" stroke-width="5"/><path d="M38 38H8M18 28 8 38l10 10" fill="none" stroke="#111" stroke-width="5"/><circle cx="56" cy="24" r="12" fill="none" stroke="#fff" stroke-width="3"/><text x="51" y="30" font-family="Lato,sans-serif" font-weight="900" font-size="16" fill="#fff">$</text></svg>
    </div>
    <h3>Smart Moves</h3>
  </div>
  <div class="abs feature" style="left:955px">
    <div class="badge">
      <svg width="70" height="64" viewBox="0 0 70 64"><path d="M6 4v54h60" fill="none" stroke="#111" stroke-width="3"/><rect x="16" y="38" width="9" height="18" fill="#111"/><rect x="30" y="28" width="9" height="28" fill="#111"/><rect x="44" y="34" width="9" height="22" fill="#111"/><path d="M14 30 32 18l12 6 18-16" fill="none" stroke="#fff" stroke-width="2.5" stroke-dasharray="4 3"/></svg>
    </div>
    <h3>Positive Growth</h3>
  </div>
</section>

<section class="abs about">
  <div class="abs eyebrow">About us</div>
  <h2 class="abs about-title">Welcome To <span>VORNELIX CAPITAL</span></h2>
  <div class="abs about-text">
    <p>Lorem Ipsum is simply dummy text of the printing and typesetting industry. Lorem Ipsum has been the industry's standard dummy text ever since the 1500s, when an unknown printer took a galley of type and scrambled it to make a type specimen book.</p>
    <p>It has survived not only five centuries, but also the leap into electronic typesetting, remaining essentially unchanged. It was popularised in the 1960s with the release of Letraset sheets containing.</p>
  </div>
  <div class="abs btn-gold">LEARN MORE</div>

  <form class="abs quote" role="img" aria-label="Quote form over a dim glass tower backdrop">
    <h2>REQUEST FREE QUOTE</h2>
    <div class="field" style="top:93px"><svg width="14" height="14" viewBox="0 0 14 14"><circle cx="7" cy="4" r="3.5" fill="#111"/><path d="M0 14a7 6 0 0 1 14 0z" fill="#111"/></svg>Name</div>
    <div class="field" style="top:136px"><svg width="14" height="14" viewBox="0 0 24 24"><path fill="#111" d="M6.6 10.8a15.1 15.1 0 0 0 6.6 6.6l2.2-2.2c.3-.3.7-.4 1-.2 1.1.4 2.3.6 3.6.6.6 0 1 .4 1 1V20c0 .6-.4 1-1 1C10.6 21 3 13.4 3 4c0-.6.4-1 1-1h3.5c.6 0 1 .4 1 1 0 1.3.2 2.5.6 3.6.1.3 0 .7-.2 1z"/></svg>Contact No</div>
    <div class="field" style="top:179px"><svg width="14" height="11" viewBox="0 0 14 11"><rect x=".5" y=".5" width="13" height="10" fill="none" stroke="#111"/><path d="M.5.5 7 6l6.5-5.5" fill="none" stroke="#111"/></svg>Email</div>
    <div class="field msg" style="top:220px"><svg width="14" height="14" viewBox="0 0 14 14"><rect x=".5" y="2.5" width="11" height="11" fill="none" stroke="#111"/><path d="M5 9l1-3 7-6 1 1-7 7z" fill="#111"/></svg>Message...</div>
    <div class="btn-light">REQUEST FREE QUOTE</div>
  </form>
</section>

<section class="projects">
  <div class="abs eyebrow">Our Work</div>
  <h2 class="abs projects-title">Latest Finished <span>PROJECTS</span></h2>
  <div class="photo" role="img" aria-label="Modern office building with glass atrium under a blue sky" style="left:78px;top:1638px;width:688px;height:311px;background:linear-gradient(180deg,#5f8fd0 0%,#a9c6ea 45%,#c9cdd2 62%,#6f8d4a 100%)"></div>
  <div class="photo" role="img" aria-label="Cobbled residential street lined with colourful terraced houses" style="left:789px;top:1638px;width:334px;height:311px;background:linear-gradient(180deg,#dfe6ee 0%,#9c7c6e 40%,#5f6b4e 70%,#6d665e 100%)"></div>
  <div class="photo" role="img" aria-label="Brick and glass campus building with landscaped lawn" style="left:78px;top:1973px;width:333px;height:313px;background:linear-gradient(180deg,#4d7fc4 0%,#9dbbe0 30%,#8c5b46 55%,#6c8a48 100%)"></div>
  <div class="abs feature-card" role="img" aria-label="Timber-framed property exterior">
    <div class="overlay">
      <div class="label">Property Name</div>
      <h3>PROJECT NAME</h3>
      <p>Lorem Ipsum is simply dummy text of the printing and typesetting industry. Lorem Ipsum has been the industry's standard dummy text.</p>
    </div>
  </div>
</section>

<footer>
  <div class="abs footer" role="img" aria-label="Dark city skyline silhouette behind footer content">
    <div class="abs footer-brand"><span class="dot"></span>VORNELIX</div>
    <p class="abs footer-about">Lorem Ipsum is simply dummy text of the printing and typesetting industry.</p>
    <div class="abs divider" style="left:411px"></div>
    <div class="abs contact-row" style="top:70px">
      <svg width="18" height="16" viewBox="0 0 18 16"><path d="M9 1 1 8h2v7h4v-4h4v4h4V8h2z" fill="#8a8a8a"/></svg>
      <span style="width:240px">123,Lorem Ipsum has been the industry's standard dummy text, Country,123456.</span>
    </div>
    <div class="abs contact-row" style="top:142px">
      <svg width="16" height="16" viewBox="0 0 24 24"><path fill="#8a8a8a" d="M6.6 10.8a15.1 15.1 0 0 0 6.6 6.6l2.2-2.2c.3-.3.7-.4 1-.2 1.1.4 2.3.6 3.6.6.6 0 1 .4 1 1V20c0 .6-.4 1-1 1C10.6 21 3 13.4 3 4c0-.6.4-1 1-1h3.5c.6 0 1 .4 1 1 0 1.3.2 2.5.6 3.6.1.3 0 .7-.2 1z"/></svg>
      <span>(555) 014 2290</span>
    </div>
    <div class="abs contact-row" style="top:180px">
      <svg width="16" height="12" viewBox="0 0 16 12"><rect width="16" height="12" fill="#8a8a8a"/><path d="M0 0l8 6 8-6" fill="none" stroke="#111" stroke-width="1.2"/></svg>
      <span>info@vornelix.com</span>
    </div>
    <div class="abs divider" style="left:766px"></div>
    <div class="abs links-title">Important Link</div>
    <ul class="abs links" style="left:822px"><li>Home</li><li>About Us</li><li>Services</li><li>Returns</li></ul>
    <ul class="abs links" style="left:928px"><li>Projects</li><li>Contact Us</li></ul>
  </div>
  <div class="abs copyright">© <strong>2018 VORNELIX CAPITAL</strong> - All rights reserved.</div>
</footer>

</body>
</html>
```